RUVO WARE LTD

Advertisement to get more schools:
use website https://www.ruvo-ware.co.uk for logos etc.
ICT Service Level Agreements for as little as £2000 per year
Unlimited Remote, phone and email support
Unlimited Call outs included
90% fix time within 30 minutes of ticket submission
Extra support during Scolvar inspections
GDPR service included

Education

```html
<!DOCTYPE html>
<html lang="en">
<head>
<meta charset="utf-8">
<title>Ruvo Ware – ICT Support for Education</title>
<link href="https://fonts.googleapis.com/css2?family=Roboto:wght@400;500;700&family=Work+Sans:wght@700&display=swap" rel="stylesheet">
<style>
  :root{
    --brand-blue:#0f6cb6;
    --brand-orange:#f07c41;
    --ink:#3d3d3d;
    --body-text:#666;
    --light-bg:#f4f4f4;
    --white:#fff;
  }
  *{box-sizing:border-box;margin:0;padding:0}
  html,body{width:681px;height:1200px;overflow:hidden;background:var(--white)}
  body{font-family:"Roboto",sans-serif;position:relative}
  .flyer{position:relative;width:681px;height:1200px;overflow:hidden}

  .site-header{position:absolute;top:0;left:0;width:681px;height:80px;background:var(--white);border-bottom:5px solid var(--brand-orange)}
  .brand{position:absolute;left:85px;top:18px;display:flex;align-items:center;gap:8px}
  .brand-mark{width:22px;height:22px;background:var(--brand-blue)}
  .brand-name{font-family:"Roboto",sans-serif;font-weight:700;font-size:24px;color:var(--brand-blue);letter-spacing:.5px}
  .header-phone{position:absolute;right:85px;top:16px;display:flex;align-items:center;gap:19px}
  .phone-badge{width:44px;height:44px;border-radius:50%;background:var(--brand-orange);display:flex;align-items:center;justify-content:center}
  .header-phone span{font-weight:500;font-size:16px;color:var(--ink)}

  .hero{position:absolute;top:80px;left:0;width:681px;height:340px;background:linear-gradient(100deg,#0b2f55 0%,#10518c 45%,#1c70b0 75%,#0e3e6d 100%)}
  .hero-box{position:absolute;left:85px;top:85px;width:512px;height:170px;border:2px solid var(--white);background:rgba(6,30,60,.55);text-align:center;color:var(--white);padding-top:29px}
  .hero-title{font-family:"Roboto",sans-serif;font-weight:700;font-size:22px;line-height:33px}
  .hero-sub{font-weight:500;font-size:15px;line-height:24px;margin-top:6px}

  .about{position:absolute;top:420px;left:0;width:681px;height:237px;background:var(--light-bg);text-align:center}
  .section-title{font-family:"Work Sans",sans-serif;font-weight:700;font-size:25px;color:var(--ink)}
  .accent{color:var(--brand-orange)}
  .about .section-title{margin-top:51px}
  .about p{width:500px;margin:15px auto 0;font-size:12px;line-height:22px;color:var(--body-text)}

  .services{position:absolute;top:657px;left:0;width:681px;height:331px;background:var(--white)}
  .services .section-title{position:absolute;left:85px;top:23px}
  .service-list{position:absolute;left:85px;top:70px;width:220px;list-style:none}
  .service-list li{position:relative;padding-left:33px;font-size:13px;line-height:20.5px;color:var(--body-text);margin-bottom:7px}
  .service-list svg{position:absolute;left:0;top:4px}
  .photo-accent{position:absolute;left:426px;top:0;width:255px;height:255px;background:linear-gradient(135deg,#f08a52,#e6733a 60%,#d86a35)}
  .photo-class{position:absolute;left:340px;top:75px;width:256px;height:256px;background:linear-gradient(160deg,#9fb7a2 0%,#6f8a78 35%,#4d5d63 65%,#7a7f86 100%)}

  .site-footer{position:absolute;top:988px;left:0;width:681px;height:212px;background:linear-gradient(180deg,#1170bb,#0c62a8);text-align:center;color:var(--white)}
  .footer-brand{display:flex;justify-content:center;align-items:center;gap:8px;margin-top:40px}
  .footer-brand .brand-mark{background:var(--white)}
  .footer-brand .brand-name{color:var(--white)}
  .footer-contact{display:flex;justify-content:center;align-items:center;gap:12px;margin-top:34px;font-weight:500;font-size:16px}
  .footer-contact .divider{margin:0 12px}
  .copyright{font-size:11px;margin-top:12px}
  .social{display:flex;justify-content:center;gap:4px;margin-top:15px}
  .social span{width:29px;height:29px;border-radius:50%;background:var(--white)}
  .social span:first-child{background:var(--brand-orange)}
</style>
</head>
<body>
<div class="flyer">
  <header class="site-header">
    <div class="brand"><span class="brand-mark"></span><span class="brand-name">RUVO WARE</span></div>
    <div class="header-phone">
      <div class="phone-badge">
        <svg width="14" height="14" viewBox="0 0 24 24"><path fill="#fff" d="M6.6 10.8a15.1 15.1 0 0 0 6.6 6.6l2.2-2.2a1 1 0 0 1 1-.25 11.4 11.4 0 0 0 3.6.57 1 1 0 0 1 1 1V20a1 1 0 0 1-1 1A17 17 0 0 1 3 4a1 1 0 0 1 1-1h3.5a1 1 0 0 1 1 1c0 1.25.2 2.45.57 3.6a1 1 0 0 1-.25 1z"/></svg>
      </div>
      <span>0161 555 0184</span>
    </div>
  </header>

  <section class="hero" role="img" aria-label="Photo of a student wearing a virtual reality headset in a classroom">
    <div class="hero-box">
      <h1 class="hero-title">EDUCATION, SUPPORT AND<br>INSTALLATION OF ALL TECHNOLOGIES</h1>
      <p class="hero-sub">We offer fast, flexible, reliable and cost-effective ICT<br>support for Education</p>
    </div>
  </section>

  <section class="about">
    <h2 class="section-title">ABOUT <span class="accent">RUVO WARE</span></h2>
    <p>Ruvo Ware, is a registered UK Limited Company. Our goal is to provide comprehensive ICT support along with excellent customer service to the education sector. We offer support in all aspects of ICT in education, from technical faults to assisting teachers and coordinators to meet the requirements of the computing curriculum</p>
  </section>

  <section class="services">
    <div class="photo-accent" role="img" aria-label="Orange-tinted photo of children building with construction kits"></div>
    <div class="photo-class" role="img" aria-label="Photo of pupils working at computers in a classroom"></div>
    <h2 class="section-title"><span class="accent">WHAT</span> WE DO</h2>
    <ul class="service-list">
      <li><svg width="12" height="12" viewBox="0 0 12 12"><circle cx="6" cy="6" r="6" fill="#0f6cb6"/><path d="M3 6h5M6 3.5 8.5 6 6 8.5" stroke="#fff" stroke-width="1.6" fill="none"/></svg>ICT SLA agreements for as little as £2000 per year</li>
      <li><svg width="12" height="12" viewBox="0 0 12 12"><circle cx="6" cy="6" r="6" fill="#0f6cb6"/><path d="M3 6h5M6 3.5 8.5 6 6 8.5" stroke="#fff" stroke-width="1.6" fill="none"/></svg>Unlimited Remote, phone and email support</li>
      <li><svg width="12" height="12" viewBox="0 0 12 12"><circle cx="6" cy="6" r="6" fill="#0f6cb6"/><path d="M3 6h5M6 3.5 8.5 6 6 8.5" stroke="#fff" stroke-width="1.6" fill="none"/></svg>Unlimited Call outs included</li>
      <li><svg width="12" height="12" viewBox="0 0 12 12"><circle cx="6" cy="6" r="6" fill="#0f6cb6"/><path d="M3 6h5M6 3.5 8.5 6 6 8.5" stroke="#fff" stroke-width="1.6" fill="none"/></svg>90% fix time within 30 minutes of ticket submission</li>
      <li><svg width="12" height="12" viewBox="0 0 12 12"><circle cx="6" cy="6" r="6" fill="#0f6cb6"/><path d="M3 6h5M6 3.5 8.5 6 6 8.5" stroke="#fff" stroke-width="1.6" fill="none"/></svg>Extra support during Scolvar inspections</li>
      <li><svg width="12" height="12" viewBox="0 0 12 12"><circle cx="6" cy="6" r="6" fill="#0f6cb6"/><path d="M3 6h5M6 3.5 8.5 6 6 8.5" stroke="#fff" stroke-width="1.6" fill="none"/></svg>GDPR service included</li>
    </ul>
  </section>

  <footer class="site-footer">
    <div class="footer-brand"><span class="brand-mark"></span><span class="brand-name">RUVO WARE</span></div>
    <div class="footer-contact">
      <svg width="14" height="14" viewBox="0 0 24 24"><path fill="#f07c41" d="M6.6 10.8a15.1 15.1 0 0 0 6.6 6.6l2.2-2.2a1 1 0 0 1 1-.25 11.4 11.4 0 0 0 3.6.57 1 1 0 0 1 1 1V20a1 1 0 0 1-1 1A17 17 0 0 1 3 4a1 1 0 0 1 1-1h3.5a1 1 0 0 1 1 1c0 1.25.2 2.45.57 3.6a1 1 0 0 1-.25 1z"/></svg>
      <span>0161 555 0184</span>
      <span class="divider">|</span>
      <svg width="16" height="13" viewBox="0 0 16 13"><rect width="16" height="13" rx="1.5" fill="#f07c41"/><path d="M1 1.5 8 7l7-5.5" stroke="#1170bb" stroke-width="1.4" fill="none"/></svg>
      <span>info@ruvo-ware.co.uk</span>
    </div>
    <p class="copyright">© 2022 RUVO WARE / All Rights Reserved</p>
    <div class="social" aria-label="Social links"><span></span><span></span><span></span></div>
  </footer>
</div>
</body>
</html>
```